Quintel Packaging Business Card

Project Overview
We are seeking a modern, minimalist business card that effectively represents our company while making a bold and lasting impression. The design should reflect trust, professionalism, and innovation, reinforcing our expertise in custom plastic manufacturing for warehouse and distribution centers.

Provided Assets & Specifications
Logo: We will provide our official logo for integration into the design.
Design Files: Photoshop (PSD) files for our printing specifications will be supplied.

Card Size & Material:
Dimensions: 3.5" x 2"
Material: 1/8" Radius Plastic Business Cards with 1/8" Rounded Corners
Clear plastic background—the design should strategically incorporate transparency.
Orientation: The card should be designed in landscape format for a sleek and professional presentation.

Design Requirements:
Logo Prominence
The logo must be the focal point of the card.
Space should be used effectively to draw attention to the logo while maintaining a minimalist layout.

Clear Plastic Integration
The transparent background should create the illusion of blank space, enhancing the modern and high-quality feel.
Avoid any frosted effects—we do not want white areas to appear semi-transparent.

Minimalist & Impactful
Clean, structured, and easy to read at a glance.
Focus on sharp contrast to ensure legibility and visibility.
The design should instill confidence and reflect our role as a leading plastics manufacturer.

Color Palette & Contrast
Primary Colors: Blue, Black, White, and Grey
Use bold black or blue for text and key elements to ensure they stand out against the clear plastic.
Avoid light, pastel, or neon colors that may fade into the plastic background.
No frosted or semi-transparent white—we do not want a cloudy effect.

Typography & Information Hierarchy
Bold, modern typography—clear, professional, and highly legible.
The business card should highlight:
Company Logo (Primary Focus)
Full Name & Title
Phone Number
Email
Website

Brand Representation
The card should reflect our expertise in manufacturing high-quality custom plastics for large-scale packaging and distribution businesses.
Our clients rely on us to enhance their brand presence through custom plastic solutions, and our business cards should reinforce that sense of precision and trust.

Final Considerations
Utilize the clear plastic effectively to differentiate our brand from standard business cards.
Maintain a sleek, professional aesthetic while ensuring all text and elements remain legible.
The design should align with our industry, conveying reliability and innovation.
We look forward to seeing a design that captures our brand identity, maximizes the clear plastic medium, and makes a strong, professional impact on our clients.

```html
<!DOCTYPE html>
<html lang="en">
<head>
<meta charset="utf-8">
<title>Quintel Packaging Business Card</title>
<link rel="stylesheet" href="https://fonts.googleapis.com/css2?family=Lato:wght@400;700&display=swap">
<style>
  :root {
    --page-bg: #d9dcdf;
    --card-clear: #eef2f4;
    --card-edge: #c3cacf;
    --ink-dark: #3a3a3c;
    --ink-mid: #4a4a4d;
    --brand-blue: #1f6d8e;
    --mark-dark: #1e1e20;
  }
  * { box-sizing: border-box; margin: 0; padding: 0; }
  html, body {
    width: 1200px; height: 968px; overflow: hidden;
    background: var(--page-bg);
    font-family: "Lato", Arial, sans-serif;
  }
  .card {
    position: absolute; left: 170px; top: 239px;
    width: 860px; height: 491px;
    background: var(--card-clear);
    border: 1px solid var(--card-edge);
    border-radius: 22px;
  }
  .wordmark {
    position: absolute; left: 46px; top: 52px;
    font-size: 40px; font-weight: 700; color: var(--ink-dark);
    letter-spacing: 0.5px;
  }
  .brand-square {
    position: absolute; left: 500px; top: 96px;
    width: 300px; height: 300px;
    background: var(--brand-blue);
  }
  .person-name {
    position: absolute; left: 46px; top: 180px;
    font-size: 31px; font-weight: 700; color: var(--ink-dark);
  }
  .person-title {
    position: absolute; left: 46px; top: 225px;
    font-size: 21px; color: var(--ink-mid);
  }
  .contact-list { position: absolute; left: 46px; top: 283px; list-style: none; }
  .contact-item {
    display: flex; align-items: center; gap: 20px;
    height: 36px; font-size: 21px; color: var(--ink-mid);
  }
  .contact-icon { width: 22px; height: 22px; fill: var(--brand-blue); flex: none; }
  .address {
    position: absolute; left: 46px; top: 397px;
    font-size: 21px; line-height: 31px; color: var(--ink-dark);
  }
</style>
</head>
<body>
  <div class="card">
    <div class="wordmark">Quintel Packaging</div>
    <div class="brand-square"></div>

    <div class="person-name">DANIEL HARPER</div>
    <div class="person-title">Owner</div>

    <ul class="contact-list">
      <li class="contact-item">
        <svg class="contact-icon" viewBox="0 0 24 24" aria-hidden="true"><path d="M6.6 10.8c1.4 2.8 3.8 5.1 6.6 6.6l2.2-2.2c.3-.3.7-.4 1-.2 1.1.4 2.3.6 3.6.6.6 0 1 .4 1 1V20c0 .6-.4 1-1 1C10.6 21 3 13.4 3 4c0-.6.4-1 1-1h3.5c.6 0 1 .4 1 1 0 1.3.2 2.5.6 3.6.1.3 0 .7-.2 1z"/></svg>
        <span>044-987 654 321</span>
      </li>
      <li class="contact-item">
        <svg class="contact-icon" viewBox="0 0 24 24" aria-hidden="true"><path d="M2 5h20v2l-10 6L2 7z"/><path d="M2 9l10 6 10-6v10H2z"/></svg>
        <span>hello@quintelpack.com</span>
      </li>
      <li class="contact-item">
        <svg class="contact-icon" viewBox="0 0 24 24" aria-hidden="true"><circle cx="12" cy="12" r="10"/><path d="M2 12h20M12 2c3 3 3 17 0 20M12 2c-3 3-3 17 0 20" stroke="#eef2f4" stroke-width="1.5" fill="none"/></svg>
        <span>www.quintelpack.com</span>
      </li>
    </ul>

    <div class="address">87, Harbour Works Road<br>45610, Westland</div>
  </div>
</body>
</html>
```